Marlowe Group needs a business card

I would like the card to be simple but modern and elegant.
I like black and white.
or black and gold.
we are a private finance lender and also are involved in property and property developments.

please look at the business card photos i provided i would like M.G only one one side and all the other details on the other side use fonts that tie in with my theme.

Industry/Entity Type

Finance

Contact Information for Business Card

Marlowe Group (M.G) Daniel Marlowe M: 0413586207 E: danmarl@inboxmail.test

Font styles to use
Other font styles liked:
• Use fonts that would reflect our business

Colors
000000
ffffff

Requirements
Must have
• one side of details
• other side has either M.G or Marlowe Group like in the photos provided

```html
<!DOCTYPE html>
<html lang="en">
<head>
<meta charset="utf-8">
<title>Marlowe Group – Business Card</title>
<link rel="stylesheet" href="https://fonts.googleapis.com/css2?family=Open+Sans:wght@400;600;700;800&display=swap">
<style>
  :root {
    --backdrop: #6e4c34;
    --card-white: #ffffff;
    --ink-black: #000000;
    --text-grey: #555555;
    --band-grey: #6b6b6b;
    --gold: #c9a73e;
  }
  * { margin: 0; padding: 0; box-sizing: border-box; }
  html, body {
    width: 1200px;
    height: 987px;
    overflow: hidden;
  }
  body {
    background: var(--backdrop);
    font-family: "Open Sans", Arial, sans-serif;
    position: relative;
  }
  .card {
    position: absolute;
    left: 293px;
    width: 615px;
    height: 352px;
    box-shadow: 0 4px 10px rgba(0, 0, 0, 0.35);
  }
  .card-front {
    top: 130px;
    background: var(--card-white);
  }
  .card-back {
    top: 506px;
    background: var(--ink-black);
    display: flex;
    align-items: center;
    justify-content: center;
  }
  .brand-name {
    position: absolute;
    left: 26px;
    top: 50px;
    font-weight: 800;
    font-size: 31px;
    letter-spacing: 1px;
    line-height: 1;
    color: var(--ink-black);
    text-transform: uppercase;
  }
  .contact {
    position: absolute;
    left: 372px;
    top: 190px;
    color: var(--text-grey);
  }
  .contact-name {
    font-weight: 600;
    font-size: 23px;
    color: var(--ink-black);
    margin-bottom: 12px;
    line-height: 1.2;
  }
  .contact-line {
    font-size: 16px;
    line-height: 24px;
  }
  .contact-label {
    font-weight: 700;
    color: var(--ink-black);
  }
  .front-band {
    position: absolute;
    left: 0;
    bottom: 0;
    width: 615px;
    height: 24px;
    display: block;
  }
  .monogram {
    font-weight: 800;
    font-size: 106px;
    letter-spacing: 4px;
    color: var(--gold);
    line-height: 1;
  }
</style>
</head>
<body>
  <section class="card card-front" aria-label="Business card front">
    <div class="brand-name">Marlowe Group</div>
    <div class="contact">
      <p class="contact-name">Daniel Marlowe</p>
      <p class="contact-line"><span class="contact-label">Cell :</span> 0413586207</p>
      <p class="contact-line">danmarl@inboxmail.test</p>
      <p class="contact-line">www.marlowegroup.test</p>
    </div>
    <svg class="front-band" viewBox="0 0 615 24" aria-hidden="true">
      <polygon points="0,0 388,0 381,24 0,24" fill="var(--ink-black)"/>
      <polygon points="393,0 615,0 615,24 386,24" fill="var(--band-grey)"/>
    </svg>
  </section>

  <section class="card card-back" aria-label="Business card back">
    <div class="monogram">M.G</div>
  </section>
</body>
</html>
```